Modern/Bold/Unique Prenatal Vitamin label redesign

We are in need of a design update for our Prenatal Vitamin label. We want to modernize our label and give it a fresh feel.
It should bring a feeling of fun, joy, and sophistication, but also be bold/edgy/unique and portray Trust and Authority. Our buyers are mainly mothers in the age range of 25-34 who are pregnant or breastfeeding.
I will attach our current label design, as well as some inspiration to go off of.
We like the idea of having a clean, easy to read label label with bold/vibrant colors and fonts. We like the idea of having some retro vibes in it as well
Please see the attached artwork for design inspiration (New Design Idea). We like the idea of having a pregnant mother image like the attachment on the label, with the rest of the label being white. Please come up with a unique drawing/image for the design. We cannot use a copied image or stock image.
We look forward to working with you!

```html
<!DOCTYPE html>
<html lang="en">
<head>
<meta charset="utf-8">
<title>Nestling Bloom Essential Label</title>
<link href="https://fonts.googleapis.com/css2?family=Catamaran:wght@600;800&family=Didact+Gothic&display=swap" rel="stylesheet">
<style>
  :root {
    --page: #ffffff;
    --label-light: #f7f8fa;
    --label-shade: #e9eaee;
    --magenta: #9b1a6a;
    --magenta-deep: #7e1560;
    --magenta-bright: #c0267a;
    --glow: #f7a27e;
    --glow-core: #fff6ef;
    --pink-sheen: #d98ccd;
    --ink-grey: #555a60;
  }
  * { box-sizing: border-box; margin: 0; padding: 0; }
  html, body {
    width: 1099px;
    height: 1200px;
    overflow: hidden;
    background: var(--page);
  }
  .label {
    position: absolute;
    left: 100px;
    top: 50px;
    width: 900px;
    height: 1100px;
    background: linear-gradient(90deg, var(--label-shade) 0%, var(--label-light) 30%, var(--label-light) 70%, var(--label-shade) 100%);
    overflow: hidden;
  }
  .hero-art {
    position: absolute;
    left: 100px;
    top: 37px;
    width: 700px;
    height: 580px;
    border-radius: 46% 50% 40% 44%;
    background:
      radial-gradient(circle at 50% 62%, var(--glow-core) 0%, var(--glow) 14%, var(--magenta-bright) 34%, var(--magenta) 58%, rgba(155, 26, 106, 0) 76%);
  }
  .brand {
    position: absolute;
    left: 0;
    width: 100%;
    top: 620px;
    text-align: center;
    font-family: "Catamaran", sans-serif;
    font-weight: 800;
    font-size: 132px;
    line-height: 1;
    letter-spacing: -2px;
    color: var(--magenta);
  }
  .product-name {
    position: absolute;
    left: 0;
    width: 100%;
    top: 880px;
    text-align: center;
    font-family: "Catamaran", sans-serif;
    font-weight: 800;
    font-size: 56px;
    line-height: 1;
    letter-spacing: 1px;
    color: var(--magenta);
  }
  .tagline {
    position: absolute;
    left: 0;
    width: 100%;
    top: 955px;
    text-align: center;
    font-family: "Didact Gothic", sans-serif;
    font-size: 31px;
    line-height: 41px;
    color: var(--ink-grey);
  }
  .tagline .audience { display: block; color: var(--magenta); }
  .count-badge {
    position: absolute;
    left: 769px;
    top: 861px;
    width: 116px;
    height: 116px;
    border-radius: 50%;
    background: #ffffff;
    text-align: center;
    font-family: "Didact Gothic", sans-serif;
    color: var(--ink-grey);
  }
  .count-badge .count {
    display: block;
    font-family: "Catamaran", sans-serif;
    font-weight: 600;
    font-size: 56px;
    line-height: 1;
    padding-top: 10px;
    color: var(--magenta-deep);
  }
  .count-badge .unit {
    display: block;
    font-size: 14px;
    line-height: 18px;
  }
  .base-stripe {
    position: absolute;
    left: 0;
    bottom: 0;
    width: 100%;
    height: 18px;
    background: linear-gradient(90deg, var(--magenta) 0%, var(--magenta-bright) 45%, var(--pink-sheen) 78%, var(--magenta) 100%);
  }
</style>
</head>
<body>
  <main class="label">
    <div class="hero-art" role="img" aria-label="Stippled magenta illustration of a mother and baby in profile, close together, with a warm glowing heart shape between them"></div>
    <h1 class="brand">nestling</h1>
    <h2 class="product-name">BLOOM ESSENTIAL</h2>
    <p class="tagline">Daily Whole-Body Nutrient Blend For <span class="audience">Mom &amp; Little One</span></p>
    <div class="count-badge">
      <span class="count">90</span>
      <span class="unit">VEGGIE</span>
      <span class="unit">CAPSULES</span>
    </div>
    <div class="base-stripe"></div>
  </main>
</body>
</html>
```